Stationery for a private security company, "Brenmoor Security Services Ltd."

Needed is a stationery design for a private security company. The designs must show professionalism and that our company mean nothing but business. Watermark of the company logo on the letterhead page is also a must. The final design must represent innovation and professionalism. It would be great if designers could integrate the colours black and silver onto the cards and letterheads..

Thank you

```html
<!DOCTYPE html>
<html lang="en">
<head>
<meta charset="utf-8">
<title>Brenmoor Security Services Ltd. – Stationery</title>
<link rel="stylesheet" href="https://fonts.googleapis.com/css2?family=Open+Sans:wght@400;700&family=Noto+Serif:wght@400&display=swap">
<style>
  :root{
    --bg:#4a2c1e;
    --paper:#ffffff;
    --paper-shade:#f1f1f1;
    --ink:#111111;
    --black:#0d0d0d;
    --silver:#b4bfc3;
    --steel:#6f8088;
    --watermark:#ececec;
    --rule:#333333;
    --label:#ffffff;
  }
  *{box-sizing:border-box;margin:0;padding:0}
  html,body{width:1200px;height:515px;overflow:hidden;background:var(--bg)}
  .canvas{position:relative;width:1200px;height:515px;font-family:"Open Sans",sans-serif;color:var(--ink)}
  .sheet{position:absolute;background:var(--paper);box-shadow:0 1px 4px rgba(0,0,0,.35);overflow:hidden}
  .sheet svg.footer{position:absolute;left:0;bottom:0}
  .brand{position:absolute;font-family:"Open Sans",sans-serif;font-weight:700;color:var(--ink);text-transform:uppercase;line-height:1.15;letter-spacing:.02em}
  .brand-mark{display:inline-block;width:7px;height:7px;border-radius:50%;background:var(--ink);margin-right:4px;vertical-align:middle}
  .watermark{position:absolute;font-family:"Open Sans",sans-serif;font-weight:700;color:var(--watermark);text-transform:uppercase;line-height:1}
  .contact{position:absolute;font-family:"Noto Serif",serif;font-size:6px;line-height:8.6px;border-left:1px solid #999;padding-left:4px;color:var(--ink)}
  .contact span::before{content:"";display:inline-block;width:4px;height:4px;border-radius:50%;background:var(--ink);margin-right:3px;vertical-align:middle}
  .address{position:absolute;font-family:"Noto Serif",serif;color:#fff;letter-spacing:.08em;text-align:center}

  .letterhead{top:30px;width:343px;height:444px}
  .letterhead.plain{left:43px}
  .letterhead.fax{left:397px;background:linear-gradient(160deg,var(--paper) 0%,var(--paper-shade) 100%)}
  .fax-title{position:absolute;left:10px;top:94px;font-size:21px;font-weight:400;letter-spacing:.02em}
  .fax-fields{position:absolute;left:10px;top:130px;width:292px}
  .fax-row{display:flex;gap:12px;height:18.5px;align-items:flex-end}
  .fax-field{flex:1;border-bottom:1px solid var(--rule);font-size:5.5px;padding-bottom:2px}
  .fax-field.right{flex:0 0 118px}
  .fax-checks{position:absolute;left:10px;top:246px;display:flex;gap:17px;font-size:5.5px}
  .fax-checks span::before{content:"";display:inline-block;width:6px;height:6px;border:1px solid var(--rule);margin-right:4px;vertical-align:middle}

  .envelope{width:384px;height:171px}
  .envelope.back-silver{left:772px;top:18px}
  .envelope.back-black{left:760px;top:93px;background:#f2f2f2}
  .envelope.front{left:745px;top:194px;width:383px;height:172px}
  .envelope svg.flap{position:absolute;left:0;top:0}

  .card{width:141px;height:80px}
  .card.front{left:766px;top:394px}
  .card.back{left:916px;top:396px;background:var(--black)}
  .card-contact{position:absolute;left:4px;top:33px;font-family:"Noto Serif",serif;font-size:3.6px;line-height:5.2px}

  .option-label{position:absolute;top:484px;font-size:22px;color:var(--label);font-weight:400}
</style>
</head>
<body>
<main class="canvas">

  <!-- Letterhead -->
  <section class="sheet letterhead plain" aria-label="Letterhead">
    <div class="brand" style="left:12px;top:22px;font-size:8px"><i class="brand-mark"></i>Brenmoor<br><span style="font-size:5px;margin-left:11px">Security Services Ltd.</span></div>
    <div class="contact" style="left:226px;top:16px">
      <span>123-456-7890</span><br><span>123-456-7856</span><br><span>hello@brenmoorsecurity.com</span><br><span>www.brenmoorsecurity.com</span>
    </div>
    <div class="watermark" style="left:12px;top:330px;font-size:30px">Brenmoor</div>
    <svg class="footer" width="343" height="36" viewBox="0 0 343 36">
      <path d="M0,12 L215,12 L203,22 L0,22 Z" fill="var(--silver)"/>
      <path d="M0,28 L200,28 L228,0 L343,0 L343,36 L0,36 Z" fill="var(--black)"/>
    </svg>
    <div class="address" style="left:230px;top:419px;width:110px;font-size:6.5px;line-height:9px">Street Name, City Name<br>State Zipcode</div>
  </section>

  <!-- Fax sheet -->
  <section class="sheet letterhead fax" aria-label="Fax cover sheet">
    <div class="brand" style="left:12px;top:22px;font-size:8px"><i class="brand-mark"></i>Brenmoor<br><span style="font-size:5px;margin-left:11px">Security Services Ltd.</span></div>
    <div class="contact" style="left:226px;top:16px">
      <span>123-456-7890</span><br><span>123-456-7856</span><br><span>hello@brenmoorsecurity.com</span><br><span>www.brenmoorsecurity.com</span>
    </div>
    <h1 class="fax-title">FAX</h1>
    <div class="fax-fields">
      <div class="fax-row"><div class="fax-field">To :</div><div class="fax-field right">From :</div></div>
      <div class="fax-row"><div class="fax-field">Fax :</div><div class="fax-field right">Pages :</div></div>
      <div class="fax-row"><div class="fax-field">Phone :</div><div class="fax-field right">Date :</div></div>
      <div class="fax-row"><div class="fax-field">Re :</div><div class="fax-field right">CC :</div></div>
    </div>
    <div class="fax-checks"><span>Urgent</span><span>For Review</span><span>Please Comment</span><span>Please Reply</span><span>Please Recycle</span></div>
    <svg class="footer" width="343" height="36" viewBox="0 0 343 36">
      <path d="M0,12 L215,12 L203,22 L0,22 Z" fill="var(--silver)"/>
      <path d="M0,28 L200,28 L228,0 L343,0 L343,36 L0,36 Z" fill="var(--black)"/>
    </svg>
    <div class="address" style="left:230px;top:419px;width:110px;font-size:6.5px;line-height:9px">Street Name, City Name<br>State Zipcode</div>
  </section>

  <!-- Envelope backs -->
  <section class="sheet envelope back-silver" aria-label="Envelope back, silver flap">
    <svg class="flap" width="384" height="171" viewBox="0 0 384 171">
      <path d="M0,0 L384,0 L378,28 Q370,44 340,50 L225,68 Q192,74 159,68 L44,50 Q14,44 6,28 Z" fill="var(--silver)"/>
    </svg>
    <div class="watermark" style="left:150px;top:28px;font-size:12px;color:#8e9a9e">Brenmoor</div>
  </section>

  <section class="sheet envelope back-black" aria-label="Envelope back, black flap">
    <svg class="flap" width="384" height="171" viewBox="0 0 384 171">
      <path d="M0,0 L384,0 L378,28 Q370,44 340,50 L225,68 Q192,74 159,68 L44,50 Q14,44 6,28 Z" fill="var(--black)"/>
    </svg>
    <div class="watermark" style="left:150px;top:28px;font-size:12px;color:#2b2b2b">Brenmoor</div>
  </section>

  <!-- Envelope front -->
  <section class="sheet envelope front" aria-label="Envelope front">
    <div class="watermark" style="left:6px;top:70px;font-size:26px">Brenmoor</div>
    <div class="brand" style="right:12px;top:50px;font-size:11px;text-align:right"><i class="brand-mark"></i>Brenmoor<br><span style="font-size:5.5px">Security Services Ltd.</span></div>
    <div class="address" style="right:8px;top:134px;font-size:6.5px;color:var(--ink);text-align:right">Street Name, City Name, State Zipcode</div>
    <svg class="footer" width="383" height="26" viewBox="0 0 383 26">
      <path d="M0,8 L208,8 L198,14 L0,14 Z" fill="var(--steel)"/>
      <path d="M0,18 L195,18 L213,0 L383,0 L383,26 L0,26 Z" fill="var(--black)"/>
    </svg>
    <div class="address" style="right:10px;top:154px;font-size:6.5px;color:#ddd;text-align:right">www.brenmoorsecurity.com</div>
  </section>

  <!-- Business card front -->
  <section class="sheet card front" aria-label="Business card front">
    <div class="brand" style="left:4px;top:6px;font-size:6px"><i class="brand-mark" style="width:5px;height:5px;margin-right:2px"></i>Brenmoor<br><span style="font-size:3.6px">Security Services Ltd.</span></div>
    <div class="watermark" style="left:60px;top:28px;font-size:14px">Brenmoor</div>
    <div class="card-contact">
      Street Name, City Name<br>State Zipcode<br>123-456-7890<br>123-456-7856<br>hello@brenmoorsecurity.com<br>www.brenmoorsecurity.com
    </div>
    <svg class="footer" width="141" height="10" viewBox="0 0 141 10">
      <path d="M0,6 L70,6 L78,0 L141,0 L141,10 L0,10 Z" fill="var(--black)"/>
    </svg>
    <div class="address" style="right:6px;top:71px;font-size:4.5px;letter-spacing:.02em">Your Name, Title</div>
  </section>

  <!-- Business card back -->
  <section class="sheet card back" aria-label="Business card back">
    <div class="watermark" style="left:6px;top:16px;font-size:14px;color:#3a3a3a">Brenmoor</div>
    <div class="brand" style="right:6px;top:42px;font-size:8px;color:#e6e6e6;text-align:right">Brenmoor<br><span style="font-size:4.2px">Security Services Ltd.</span></div>
  </section>

  <p class="option-label" style="left:146px">Option-1</p>
  <p class="option-label" style="left:503px">Option-2</p>
</main>
</body>
</html>
```